Tall Fern Roofing Business Card

Need a business card with the logo that was designed here

Contact Information for Business Card

Name, Title, Phone, Email, Website, Company name

```html
<!DOCTYPE html>
<html lang="en">
<head>
<meta charset="utf-8">
<title>Tall Fern Roofing – Business Card</title>
<link href="https://fonts.googleapis.com/css2?family=Open+Sans:wght@400;600;700&display=swap" rel="stylesheet">
<style>
  :root {
    --page-bg: #232323;
    --card-bg: #151516;
    --brand-blue: #1f78c8;
    --text-light: #e9e9ea;
    --emboss-tone: #2b2b2d;
    --divider: #1f78c8;
  }
  * { box-sizing: border-box; margin: 0; padding: 0; }
  html, body { width: 1200px; height: 780px; overflow: hidden; }
  body {
    background: var(--page-bg);
    font-family: "Open Sans", Arial, sans-serif;
    display: flex;
    align-items: center;
    justify-content: center;
    gap: 50px;
  }
  .card {
    width: 525px;
    height: 300px;
    background: var(--card-bg);
    border: 4px solid var(--brand-blue);
    border-radius: 26px;
    box-shadow: 0 18px 34px rgba(0,0,0,0.55);
    position: relative;
  }
  .card-front {
    display: flex;
    align-items: center;
    padding: 0 30px 0 34px;
  }
  .brand-lockup {
    display: flex;
    align-items: center;
    gap: 10px;
    width: 210px;
  }
  .brand-dot {
    width: 16px; height: 16px;
    border-radius: 50%;
    background: var(--brand-blue);
    flex: none;
  }
  .brand-name {
    color: var(--brand-blue);
    font-weight: 700;
    font-size: 24px;
    line-height: 1.1;
  }
  .divider {
    width: 1.5px;
    height: 150px;
    background: var(--divider);
    margin: 0 22px 0 10px;
  }
  .contact-block { color: var(--text-light); }
  .person-name {
    color: var(--brand-blue);
    font-weight: 700;
    font-size: 19px;
    letter-spacing: 0.3px;
    text-transform: uppercase;
  }
  .person-title { font-size: 12.5px; margin-bottom: 12px; }
  .address { font-size: 12.5px; line-height: 1.35; margin-bottom: 12px; }
  .contact-line {
    display: flex;
    align-items: center;
    gap: 7px;
    font-size: 12.5px;
    line-height: 1.45;
  }
  .contact-line svg { width: 11px; height: 11px; fill: var(--brand-blue); flex: none; }
  .card-back {
    display: flex;
    align-items: center;
    justify-content: center;
    gap: 16px;
  }
  .card-back .brand-dot { width: 30px; height: 30px; background: var(--emboss-tone); }
  .card-back .brand-name {
    color: var(--emboss-tone);
    font-size: 46px;
  }
</style>
</head>
<body>
  <section class="card card-front" aria-label="Business card front">
    <div class="brand-lockup">
      <span class="brand-dot"></span>
      <span class="brand-name">Tall Fern Roofing</span>
    </div>
    <div class="divider"></div>
    <div class="contact-block">
      <p class="person-name">Dana Whitlock</p>
      <p class="person-title">Managing Director</p>
      <p class="address">Your address, City<br>State, Zip 1234</p>
      <p class="contact-line">
        <svg viewBox="0 0 24 24"><path d="M6.6 10.8a15.1 15.1 0 0 0 6.6 6.6l2.2-2.2a1 1 0 0 1 1-.25 11.4 11.4 0 0 0 3.6.57 1 1 0 0 1 1 1V20a1 1 0 0 1-1 1A17 17 0 0 1 3 4a1 1 0 0 1 1-1h3.5a1 1 0 0 1 1 1c0 1.25.2 2.45.57 3.57a1 1 0 0 1-.25 1z"/></svg>
        123 456 789
      </p>
      <p class="contact-line">
        <svg viewBox="0 0 24 24"><path d="M2 5h20v14H2z M2 5l10 8 10-8" /></svg>
        info@yourgmail.com
      </p>
      <p class="contact-line">
        <svg viewBox="0 0 24 24"><circle cx="12" cy="12" r="10"/></svg>
        www.yourwebsite.com
      </p>
    </div>
  </section>

  <section class="card card-back" aria-label="Business card back">
    <span class="brand-dot"></span>
    <span class="brand-name">Tall Fern Roofing</span>
  </section>
</body>
</html>
```